Consultancy Business Card Design

We need a business card design for a new company based in singapore called KestrelOak. KestrelOak a boutique consultancy firm offering broad-based business solutions, from conception to re-invention, for ventures from new start-ups to long-running traditional businesses.
Its 2 main divisions (Food & Beverage Operations and Construction & Project Management) have access to a wide range of networks, knowledge bases, and resources to service its clients across numerous diverse sectors. This includes, and is not limited to, construction, F&B, and retail.
We are a company that combines the ambition, boldness and energy of one in the 20s with the dedication, level-headedness and dependability of one entering its 30s. Bridging the experiences of the old with ideals of the young, we draw on the positives of both to create a unique synergy.
We hope to see designs that fits our company profile.
Industry/Entity Type
Boutique
Contact Information for Business Card
KestrelOak(Company Name)
Marcus Thiel (Name)
Principle Consultant (Title)
F&B and Hospitality (Division)
(+65) 8043 5617 (Contact no.)
marcus@kestreloak.com.sg (Email)
Colors
Designer to choose colors to be used in the design.

```html
<!DOCTYPE html>
<html lang="en">
<head>
<meta charset="utf-8">
<title>KestrelOak Business Card</title>
<link rel="stylesheet" href="https://fonts.googleapis.com/css2?family=Montserrat:wght@400;500;600&display=swap">
<style>
  :root {
    --backdrop: #2b2b2b;
    --card: #1c1c1c;
    --card-edge: #222222;
    --accent: #e8322d;
    --accent-deep: #c4201c;
    --ink-light: #e6e6e6;
    --ink-muted: #b9b9b9;
  }
  * { box-sizing: border-box; margin: 0; padding: 0; }
  html, body {
    width: 1200px; height: 900px; overflow: hidden;
    background: var(--backdrop);
    font-family: "Montserrat", sans-serif;
  }
  .card {
    position: absolute; left: 300px;
    width: 600px; height: 343px;
    background: radial-gradient(ellipse at 50% 40%, var(--card-edge), var(--card) 75%);
    overflow: hidden;
    box-shadow: 0 12px 30px rgba(0,0,0,0.45);
  }
  .card--front { top: 90px; }
  .card--back { top: 467px; }
  .card__bands { position: absolute; inset: 0; width: 600px; height: 343px; }
  .wordmark {
    position: absolute; left: 0; right: 0;
    text-align: center;
    font-weight: 500; color: var(--ink-light);
    letter-spacing: 0.5px;
  }
  .card--front .wordmark { top: 92px; font-size: 40px; }
  .card--back .wordmark { top: 146px; font-size: 44px; }
  .contacts {
    position: absolute; left: 40px; right: 40px; top: 200px;
    display: flex; justify-content: space-between; align-items: flex-start;
  }
  .contact {
    display: flex; flex-direction: column; align-items: center; gap: 12px;
    text-align: center; font-size: 11.5px; line-height: 1.5; color: var(--ink-muted);
  }
  .contact__icon { width: 26px; height: 26px; }
  .contact__name { color: var(--ink-muted); font-weight: 500; }
  .contact__title { color: var(--accent); font-weight: 600; }
  .accent { color: var(--accent); }
  .contact__phone { color: var(--ink-light); }
</style>
</head>
<body>

<section class="card card--front" aria-label="Business card front">
  <svg class="card__bands" viewBox="0 0 600 343" aria-hidden="true">
    <polygon points="240,0 600,0 600,26 282,26" fill="var(--accent-deep)"/>
    <polygon points="254,0 600,0 600,16 276,16" fill="var(--accent)"/>
    <polygon points="0,300 70,300 52,343 0,343" fill="var(--accent)"/>
  </svg>

  <div class="wordmark">KestrelOak</div>

  <div class="contacts">
    <div class="contact">
      <svg class="contact__icon" viewBox="0 0 26 26" aria-hidden="true">
        <rect x="1" y="1" width="24" height="24" fill="none" stroke="var(--accent)" stroke-width="1.5"/>
        <circle cx="13" cy="10" r="3.5" fill="var(--accent)"/>
        <path d="M6.5 19.5c0-3.6 3-5.5 6.5-5.5s6.5 1.9 6.5 5.5z" fill="var(--accent)"/>
      </svg>
      <div>
        <div class="contact__name">Marcus Thiel</div>
        <div class="contact__title">Principle Consultant -</div>
        <div>F&amp;B and Hospitality</div>
      </div>
    </div>

    <div class="contact">
      <svg class="contact__icon" viewBox="0 0 26 26" aria-hidden="true">
        <rect x="1" y="1" width="24" height="24" fill="none" stroke="var(--accent)" stroke-width="1.5"/>
        <path d="M9 7.5l2.2-.6 1.4 3-1.4 1.2c.7 1.6 1.8 2.7 3.3 3.4l1.2-1.4 3 1.4-.6 2.2c-5 .3-9.4-4.1-9.1-9.2z" fill="var(--accent)"/>
      </svg>
      <div class="contact__phone"><span class="accent">(+65)</span> 8043 5617</div>
    </div>

    <div class="contact">
      <svg class="contact__icon" viewBox="0 0 26 26" aria-hidden="true">
        <rect x="1" y="1" width="24" height="24" fill="none" stroke="var(--accent)" stroke-width="1.5"/>
        <rect x="6.5" y="8.5" width="13" height="9" fill="var(--accent)"/>
        <path d="M6.5 8.5l6.5 5 6.5-5" fill="none" stroke="var(--card)" stroke-width="1.2"/>
      </svg>
      <div class="contact__email">marcus<span class="accent">@kestreloak.com.sg</span></div>
    </div>
  </div>
</section>

<section class="card card--back" aria-label="Business card back">
  <svg class="card__bands" viewBox="0 0 600 343" aria-hidden="true">
    <polygon points="0,317 360,317 330,343 0,343" fill="var(--accent-deep)"/>
    <polygon points="0,327 344,327 326,343 0,343" fill="var(--accent)"/>
    <polygon points="520,0 600,0 600,46" fill="var(--accent)"/>
  </svg>
  <div class="wordmark">KestrelOak</div>
</section>

</body>
</html>
```